Business Card for Vorla Parts Wholesale supplier

Hi There! I need a new business card for our company. We are specialized in selling Vorla parts, mostly we sell new LCD screens for Zelnar and Drelks. I would like to see that back in the design.

You can find the colors and logo's on our website: www.hartuvo.nl

Industry/Entity Type

Business

Contact Information for Business Card

My Details:
Tobias Lindqvist

Phone: 0031687203316
E-mail: Tobias@hartuvo.nl

Slogan: "Because Quality Matters"

Font styles to use
Sans Serif

Colors

Designer to choose colors to be used in the design.

Requirements
Must have
• A Black backside with the Hartuvo logo on it. The front side should be clean with only my contact details.
• But I'm also open for something really different or awesome!
Nice to have
• Remember that we are in the parts & repairing industry, So i'll be handing those business cards mainly to repair companies. Maybe you can do something with that thought :)

```html
<!DOCTYPE html>
<html lang="en">
<head>
<meta charset="utf-8">
<title>Hartuvo Business Card</title>
<link rel="stylesheet" href="https://fonts.googleapis.com/css2?family=Roboto:wght@400;500;700&display=swap">
<style>
  :root {
    --page-bg: #e4e4e4;
    --card-dark: #1e1e1e;
    --card-dark-deep: #141414;
    --card-light: #ffffff;
    --card-light-shade: #f1f1f1;
    --accent: #e2631f;
    --ink: #1b1b1b;
    --ink-soft: #333333;
    --white: #ffffff;
  }
  * { box-sizing: border-box; margin: 0; padding: 0; }
  html, body {
    width: 1200px;
    height: 576px;
    overflow: hidden;
  }
  body {
    position: relative;
    background: var(--page-bg);
    font-family: "Roboto", sans-serif;
  }
  .card {
    position: absolute;
    top: 138px;
    width: 484px;
    height: 294px;
    border-radius: 14px;
    overflow: hidden;
    box-shadow: 0 4px 10px rgba(0,0,0,0.22);
  }
  /* Back side */
  .card--back {
    left: 82px;
    background: var(--card-dark);
  }
  .card__photo {
    position: absolute;
    inset: 0;
    background:
      radial-gradient(ellipse at 70% 20%, #3a3a3a 0%, rgba(40,40,40,0) 55%),
      linear-gradient(160deg, #262626 0%, #2b2b2b 40%, var(--card-dark-deep) 62%, #202020 100%);
  }
  .brand-back {
    position: absolute;
    left: 104px;
    top: 120px;
    display: flex;
    align-items: center;
    gap: 22px;
  }
  .brand-back__mark {
    width: 46px;
    height: 46px;
    border-radius: 50%;
    background: var(--accent);
  }
  .brand-back__name {
    font-weight: 700;
    font-size: 52px;
    line-height: 1;
    color: var(--white);
    letter-spacing: 0.5px;
  }
  /* Front side */
  .card--front {
    left: 602px;
    width: 481px;
    background: linear-gradient(180deg, var(--card-light) 0%, var(--card-light-shade) 100%);
  }
  .brand-front {
    position: absolute;
    left: 31px;
    top: 38px;
    display: flex;
    align-items: center;
    gap: 12px;
  }
  .brand-front__mark {
    width: 56px;
    height: 56px;
    border-radius: 50%;
    background: var(--accent);
  }
  .brand-front__name {
    font-weight: 700;
    font-size: 38px;
    line-height: 1;
    color: var(--ink);
  }
  .brand-front__slogan {
    margin-top: 6px;
    font-size: 14.5px;
    color: var(--ink);
  }
  .contact {
    position: absolute;
    left: 292px;
    top: 147px;
  }
  .contact__name {
    font-weight: 700;
    font-size: 18px;
    color: var(--ink);
  }
  .contact__role {
    margin-top: 3px;
    font-size: 11px;
    color: var(--ink-soft);
  }
  .contact__list {
    list-style: none;
    margin-top: 18px;
  }
  .contact__list li {
    display: flex;
    align-items: center;
    gap: 10px;
    height: 16.5px;
    font-size: 12px;
    color: var(--ink);
  }
  .contact__list svg {
    width: 12px;
    height: 12px;
    fill: var(--accent);
    flex: none;
  }
  .card__band {
    position: absolute;
    left: 0;
    right: 0;
    bottom: 0;
    height: 13px;
    background: var(--accent);
  }
</style>
</head>
<body>
  <section class="card card--back">
    <div class="card__photo" role="img" aria-label="Dark close-up photo of a smartphone with a cracked screen"></div>
    <div class="brand-back">
      <span class="brand-back__mark"></span>
      <span class="brand-back__name">hartuvo</span>
    </div>
  </section>

  <section class="card card--front">
    <div class="brand-front">
      <span class="brand-front__mark"></span>
      <div>
        <div class="brand-front__name">hartuvo</div>
        <div class="brand-front__slogan">Because Quality Matters</div>
      </div>
    </div>

    <div class="contact">
      <div class="contact__name">Tobias Lindqvist</div>
      <div class="contact__role">Managing Director</div>
      <ul class="contact__list">
        <li>
          <svg viewBox="0 0 24 24" aria-hidden="true"><path d="M2 8c0-3 4-5 10-5s10 2 10 5v2h-5V8c-2-1-8-1-10 0v2H2z M6 11h12l3 10H3z M12 13a3 3 0 1 0 0 6a3 3 0 0 0 0-6z"/></svg>
          0031687203316
        </li>
        <li>
          <svg viewBox="0 0 24 24" aria-hidden="true"><path d="M12 2a10 10 0 1 0 0 20a10 10 0 0 0 0-20zm0 2c1 0 2.3 2 2.8 5H9.2C9.7 6 11 4 12 4zM4.3 11h3.8a17 17 0 0 0 0 2H4.3a8 8 0 0 1 0-2zm5 0h5.4a15 15 0 0 1 0 2H9.3a15 15 0 0 1 0-2zm6.6 0h3.8a8 8 0 0 1 0 2h-3.8a17 17 0 0 0 0-2zM9.2 15h5.6c-.5 3-1.8 5-2.8 5s-2.3-2-2.8-5z"/></svg>
          Tobias@hartuvo.nl
        </li>
        <li>
          <svg viewBox="0 0 24 24" aria-hidden="true"><path d="M2 5h20v14H2z M3 6l9 7l9-7v1.5l-9 7l-9-7z" fill-rule="evenodd"/></svg>
          www.hartuvo.nl
        </li>
      </ul>
    </div>

    <div class="card__band"></div>
  </section>
</body>
</html>
```